Gobal construction supply company needs new business card design

I need a business card design for my global supply company using an existing logo. i will be looking to print these on rounded corner cards with the black background version of my logo on the back. on the front white background, my logo again and my simple details.

```html
<!DOCTYPE html>
<html lang="en">
<head>
<meta charset="utf-8">
<title>Meridian Build Supply – Business Cards</title>
<link rel="stylesheet" href="https://fonts.googleapis.com/css2?family=Montserrat:wght@700&family=Open+Sans:wght@400;600&display=swap">
<style>
  :root {
    --page-bg: #d9d9d9;
    --card-dark: #1e1e1e;
    --card-light: #ffffff;
    --ink: #1b1b1b;
    --ink-soft: #444444;
    --accent: #e0141b;
    --rule: #9a9a9a;
    --white: #ffffff;
  }
  * { box-sizing: border-box; margin: 0; padding: 0; }
  html, body { width: 1200px; height: 900px; overflow: hidden; }
  body {
    background: var(--page-bg);
    position: relative;
    font-family: "Open Sans", Arial, sans-serif;
  }
  .card {
    position: absolute;
    width: 520px;
    height: 300px;
    border-radius: 26px;
  }
  .card--back {
    left: 100px; top: 130px;
    background: var(--card-dark);
    display: flex; flex-direction: column; align-items: center; justify-content: center;
  }
  .card--front {
    left: 580px; top: 470px;
    background: var(--card-light);
    box-shadow: 0 1px 3px rgba(0,0,0,0.12);
  }
  .brand {
    display: flex; align-items: center; gap: 12px;
    font-family: "Montserrat", Arial, sans-serif;
    font-weight: 700;
    letter-spacing: 0.5px;
  }
  .brand__dot {
    width: 18px; height: 18px; border-radius: 50%;
    background: var(--accent);
    flex: none;
  }
  .card--back .brand { color: var(--white); font-size: 27px; }
  .card--back .website {
    margin-top: 26px;
    color: var(--white);
    font-size: 15px;
    letter-spacing: 0.3px;
  }
  .card--front .brand {
    position: absolute; right: 34px; top: 58px;
    color: var(--ink); font-size: 22px;
  }
  .card--front .brand__dot { width: 15px; height: 15px; }
  .identity {
    position: absolute; left: 34px; top: 146px; right: 34px;
  }
  .identity__row { display: flex; align-items: center; gap: 14px; }
  .identity__name {
    font-family: "Montserrat", Arial, sans-serif;
    font-weight: 700; font-size: 21px;
    color: var(--accent);
    white-space: nowrap;
  }
  .identity__rule { flex: 1; height: 1px; background: var(--rule); }
  .identity__title { font-size: 15px; color: var(--ink-soft); margin-top: 1px; }
  .online {
    position: absolute; right: 34px; top: 184px;
    text-align: right; font-size: 14px; color: var(--ink-soft); line-height: 1.45;
  }
  .phones {
    position: absolute; left: 34px; bottom: 30px;
    font-size: 15px; color: var(--ink-soft); line-height: 1.45;
  }
  .contact-line { display: flex; align-items: center; gap: 7px; }
  .online .contact-line { justify-content: flex-end; }
  .icon { width: 12px; height: 12px; flex: none; }
</style>
</head>
<body>

  <section class="card card--back" aria-label="Business card back">
    <div class="brand"><span>MERIDIAN BUILD SUPPLY</span><span class="brand__dot"></span></div>
    <p class="website">www.meridianbuild.com</p>
  </section>

  <section class="card card--front" aria-label="Business card front">
    <div class="brand"><span>MERIDIAN BUILD SUPPLY</span><span class="brand__dot"></span></div>

    <div class="identity">
      <div class="identity__row">
        <span class="identity__name">DANIEL HARTLEY</span>
        <span class="identity__rule"></span>
      </div>
      <p class="identity__title">Managing Director</p>
    </div>

    <div class="online">
      <p class="contact-line">info@meridianbuild.com
        <svg class="icon" viewBox="0 0 12 12"><rect x="0.5" y="2" width="11" height="8" rx="1" fill="var(--accent)"/><path d="M1 2.5 6 6.5 11 2.5" stroke="#fff" stroke-width="1" fill="none"/></svg>
      </p>
      <p class="contact-line">www.meridianbuild.com
        <svg class="icon" viewBox="0 0 12 12"><circle cx="6" cy="6" r="5.5" fill="var(--accent)"/><path d="M0.5 6h11M6 0.5c-2.5 3-2.5 8 0 11M6 0.5c2.5 3 2.5 8 0 11" stroke="#fff" stroke-width="0.8" fill="none"/></svg>
      </p>
    </div>

    <div class="phones">
      <p class="contact-line">
        <svg class="icon" viewBox="0 0 12 12"><path d="M1 4c0-1.5 2-2.5 5-2.5s5 1 5 2.5v1H8.5V4h-5v1H1z" fill="var(--accent)"/><rect x="2" y="6" width="8" height="5" rx="1" fill="var(--accent)"/></svg>
        044-555 010 200
      </p>
      <p class="contact-line">
        <svg class="icon" viewBox="0 0 12 12"><rect x="2.5" y="0.5" width="7" height="11" rx="1.2" fill="none" stroke="var(--accent)" stroke-width="1.2"/><circle cx="6" cy="9.5" r="0.7" fill="var(--accent)"/></svg>
        044-555 010 201
      </p>
    </div>
  </section>

</body>
</html>
```